New Business Cards for Tormin Group

We need a new Business Card to compliment our new logo. We are a vibrant design, manufacture and install business providing recreation areas, public parks and Municipal spaces. We want business cards that are classy, modern and clean.

We have recently changed our logo, and are celebrating our 40th anniversary. We want business cards with a new modern design to reflect our status.

Target Market(s)

Customers

Contact Information for Business Card

We need all the details of our 3 offices as per the business card attached. Please disregard the old logo on the business card, the other three files show our new logo.

Requirements
Must have
• All info as per attached business card but with new logo.
Nice to have

```html
<!DOCTYPE html>
<html lang="en">
<head>
<meta charset="utf-8">
<title>Tormin Group – Business Card</title>
<link href="https://fonts.googleapis.com/css2?family=Lato:wght@400;700&display=swap" rel="stylesheet">
<style>
  :root {
    --backdrop: #5f5f5f;
    --card: #ffffff;
    --red: #e8323c;
    --ink: #333333;
    --muted: #555555;
    --rule: #777777;
    --band-grey: #4d4d4d;
  }
  * { margin: 0; padding: 0; box-sizing: border-box; }
  html, body {
    width: 1200px; height: 1200px; overflow: hidden;
    background: var(--backdrop);
    font-family: "Lato", Arial, sans-serif;
  }
  .card {
    position: absolute; left: 139px; top: 331px;
    width: 922px; height: 538px;
    background: var(--card);
    border-radius: 30px;
    overflow: hidden;
  }
  .brand {
    position: absolute; left: 32px; top: 62px;
    display: flex; align-items: center; gap: 16px;
  }
  .brand-dot { width: 64px; height: 64px; border-radius: 50%; background: var(--red); }
  .brand-name { font-size: 40px; font-weight: 700; color: var(--ink); letter-spacing: 1px; }
  .person { position: absolute; right: 35px; top: 72px; text-align: right; }
  .person-name { font-size: 31px; font-weight: 700; color: var(--red); line-height: 1.2; }
  .person-title { font-size: 21px; color: var(--ink); margin-top: 6px; }
  .contact {
    position: absolute; right: 35px; top: 233px;
    text-align: right; font-size: 17px; color: var(--ink); line-height: 31px;
  }
  .contact-row { display: flex; align-items: center; justify-content: flex-end; gap: 12px; }
  .contact-row svg { width: 12px; height: 12px; fill: var(--red); }
  .website { position: absolute; left: 32px; top: 264px; font-size: 17px; color: var(--ink); }
  .rule {
    position: absolute; left: 32px; top: 312px; width: 855px; height: 2px;
    background: var(--rule);
  }
  .office { position: absolute; top: 351px; font-size: 17px; color: var(--muted); line-height: 28px; }
  .office h2 { font-size: 22px; font-weight: 400; color: var(--red); line-height: 30px; margin-bottom: 4px; }
  .office-head { left: 32px; }
  .office-dubai { left: 353px; }
  .office-qatar { left: 647px; top: 356px; }
  .band { position: absolute; top: 506px; height: 32px; }
  .band-left { left: 0; width: 294px; background: var(--band-grey); }
  .band-mid { left: 301px; width: 327px; background: var(--red); }
  .band-right { left: 635px; right: 0; background: var(--band-grey); }
</style>
</head>
<body>
  <div class="card">
    <div class="brand">
      <div class="brand-dot"></div>
      <div class="brand-name">TORMIN GROUP</div>
    </div>

    <div class="person">
      <div class="person-name">Rami Daoudi</div>
      <div class="person-title">Managing Partner</div>
    </div>

    <div class="contact">
      <div class="contact-row">+971 (0)50 418 7390
        <svg viewBox="0 0 24 24"><path d="M6.6 10.8a15 15 0 0 0 6.6 6.6l2.2-2.2a1 1 0 0 1 1-.25 11.4 11.4 0 0 0 3.6.57 1 1 0 0 1 1 1V20a1 1 0 0 1-1 1A17 17 0 0 1 3 4a1 1 0 0 1 1-1h3.5a1 1 0 0 1 1 1c0 1.25.2 2.45.57 3.57a1 1 0 0 1-.25 1z"/></svg>
      </div>
      <div class="contact-row">rami@tormingroup.com
        <svg viewBox="0 0 24 24"><path d="M2 5h20v14H2z M2 5l10 7 10-7" /></svg>
      </div>
    </div>

    <div class="website">www.tormingroup.com</div>
    <div class="rule"></div>

    <div class="office office-head">
      <h2>Head Office</h2>
      <p>P.O. Box: 31842 Abu Dhabi. U.A.E</p>
      <p>Tel No: +971 (0)2 5873196</p>
      <p>Fax No: +971(0)2 5873197</p>
      <p>Email: sales@tormingroup.com</p>
    </div>

    <div class="office office-dubai">
      <h2>Dubai Office</h2>
      <p>P.O. Box: 472816 Dubai, U.A.E</p>
      <p>Tel No: +971 (0)4 628374</p>
      <p>Fax No: +971(0)4 628375</p>
      <p>Email: sales@tormingroup.com</p>
    </div>

    <div class="office office-qatar">
      <h2>Qater Office</h2>
      <p>P.O. Box: 20938 Doha, Qatter</p>
      <p>Tel No: +974 44517386</p>
      <p>Fax No: +971 44730518</p>
      <p>Email: sales@tormingroup.com</p>
    </div>

    <div class="band band-left"></div>
    <div class="band band-mid"></div>
    <div class="band band-right"></div>
  </div>
</body>
</html>
```